Simple and Clean business card design

We would like the design to be simple clean and to incorporate our colors.

We are open to your design and talent, we have the dots in our logo as we think of it as data points and we connect data points for people.

We are open to see the great creative and clean design you bring to the table

Contact Information for Business Card

please include: name, position, email, phone and website

Font styles to use
Sans Serif

Requirements
Must have
• my colors incorporated, simplicity
Nice to have
• lots of white space, simplicity
Should not have
• complexicity/ complex art

```html
<!DOCTYPE html>
<html lang="en">
<head>
<meta charset="utf-8">
<title>Nectra business card</title>
<link rel="stylesheet" href="https://fonts.googleapis.com/css2?family=Montserrat:wght@600&family=Arimo:wght@400;700&display=swap">
<style>
  :root {
    --backdrop: #2a2a2a;
    --card-white: #ffffff;
    --ink: #111111;
    --brand-blue: #4285f4;
    --brand-green: #34a853;
    --brand-yellow: #fbbc05;
    --brand-red: #ea4335;
  }
  * { margin: 0; padding: 0; box-sizing: border-box; }
  html, body {
    width: 1200px; height: 901px; overflow: hidden;
    background: var(--backdrop);
  }
  .stage { position: relative; width: 1200px; height: 901px; }
  .card {
    position: absolute; left: 300px; width: 600px; height: 343px;
    overflow: hidden; border-radius: 2px;
  }
  .card--front {
    top: 90px;
    background: linear-gradient(135deg, #3f7fe8 0%, #2f9a7a 55%, #3aa65a 100%);
  }
  .card--back { top: 468px; background: var(--card-white); }
  .stripe { position: absolute; display: flex; }
  .stripe span { flex: 1; }
  .stripe--front { left: 0; right: 0; bottom: 0; height: 12px; }
  .stripe--back { left: 0; top: 0; bottom: 0; width: 14px; flex-direction: column; }
  .stripe .is-blue { background: var(--brand-blue); }
  .stripe .is-green { background: var(--brand-green); }
  .stripe .is-yellow { background: var(--brand-yellow); }
  .stripe .is-red { background: var(--brand-red); }
  .wordmark {
    position: absolute; display: flex; align-items: center; gap: 12px;
    font-family: "Montserrat", sans-serif; font-weight: 600; letter-spacing: 1px; line-height: 1;
  }
  .wordmark__dot { border-radius: 50%; }
  .card--front .wordmark {
    left: 0; right: 0; top: 130px; justify-content: center;
    color: var(--card-white); font-size: 72px;
  }
  .card--front .wordmark__dot { width: 18px; height: 18px; background: var(--card-white); }
  .card--back .wordmark { left: 60px; top: 110px; color: var(--ink); font-size: 64px; }
  .card--back .wordmark__dot { width: 16px; height: 16px; background: var(--brand-blue); }
  .person {
    position: absolute; right: 36px; top: 44px; text-align: right;
    font-family: "Arimo", sans-serif;
  }
  .person__name { color: var(--brand-blue); font-weight: 700; font-size: 24px; letter-spacing: 0.5px; }
  .person__role { color: var(--ink); font-size: 16px; margin-top: 2px; }
  .contact {
    position: absolute; left: 62px; top: 208px; list-style: none;
    font-family: "Arimo", sans-serif; font-size: 18px; color: var(--ink);
  }
  .contact__item { display: flex; align-items: center; gap: 10px; height: 26px; }
  .contact__icon { width: 20px; height: 20px; flex: none; }
  .address {
    position: absolute; left: 62px; top: 298px; width: 340px;
    border-top: 1.5px solid var(--ink); padding-top: 8px;
    font-family: "Arimo", sans-serif; font-size: 18px; color: var(--ink);
  }
</style>
</head>
<body>
<main class="stage">
  <section class="card card--front" aria-label="Card front">
    <div class="wordmark"><span class="wordmark__dot"></span><span>Nectra</span></div>
    <div class="stripe stripe--front" aria-hidden="true">
      <span class="is-blue"></span><span class="is-green"></span><span class="is-yellow"></span><span class="is-red"></span>
    </div>
  </section>

  <section class="card card--back" aria-label="Card back">
    <div class="stripe stripe--back" aria-hidden="true">
      <span class="is-blue"></span><span class="is-green"></span><span class="is-yellow"></span><span class="is-red"></span>
    </div>
    <div class="person">
      <div class="person__name">Daniel Moore</div>
      <div class="person__role">Manager</div>
    </div>
    <div class="wordmark"><span class="wordmark__dot"></span><span>Nectra</span></div>
    <ul class="contact">
      <li class="contact__item">
        <svg class="contact__icon" viewBox="0 0 20 20" aria-hidden="true"><rect width="20" height="20" rx="4" fill="var(--brand-blue)"/><path d="M6 4.5c.6-.4 1.3-.3 1.6.3l1 2c.2.5 0 1-.4 1.3l-.7.5c.6 1.4 1.5 2.4 2.9 3l.5-.7c.3-.4.9-.6 1.3-.3l2 1c.5.3.7 1 .3 1.6-.6 1-1.8 1.5-3 1.1C8.1 14.5 5.6 12 4.9 8.7 4.6 6.9 5 5.3 6 4.5z" fill="#fff"/></svg>
        <span>555-014-7390</span>
      </li>
      <li class="contact__item">
        <svg class="contact__icon" viewBox="0 0 20 20" aria-hidden="true"><rect width="20" height="20" rx="4" fill="var(--brand-blue)"/><rect x="4" y="6" width="12" height="8" fill="none" stroke="#fff" stroke-width="1.4"/><path d="M4 6l6 5 6-5" fill="none" stroke="#fff" stroke-width="1.4"/></svg>
        <span>youremail@mailbox.com</span>
      </li>
      <li class="contact__item">
        <svg class="contact__icon" viewBox="0 0 20 20" aria-hidden="true"><rect width="20" height="20" rx="4" fill="var(--brand-blue)"/><circle cx="10" cy="10" r="6" fill="none" stroke="#fff" stroke-width="1.4"/><path d="M4 10h12M10 4c-2.5 3-2.5 9 0 12M10 4c2.5 3 2.5 9 0 12" fill="none" stroke="#fff" stroke-width="1.2"/></svg>
        <span>www.yourwebsite.com</span>
      </li>
    </ul>
    <p class="address">Your address, city, state, ZIP 0000</p>
  </section>
</main>
</body>
</html>
```